Food and Beverage Business Cards

We need business cards with logo designs for a consultant in the food and beverage industry. We specialize in helping restaurants fix operational and management problems.
Specific areas of expertise include:
-Steps of service
-Staff management tools
-Standard operating procedures
-Profit and loss management
-Inventory
-Point of sales
-Bar Menu
-Mystery shopper service
-Handling and managing suppliers

Target Market(s)

Restaurant and bar owners and managers

Industry/Entity Type

Business

Contact Information for Business Card

Mathieu Girardot
Q&T Consulting
phone: 15027390614
mathqt@sampleinbox.com

Font styles to use
Other font styles liked:
• Check out the screen shot font idea

Colors

Designer to choose colors to be used in the design.

Requirements
Must have
• Must include QR code (See attachment)
• Logo should reflect our specific focus on the drinks side of the industry.
• Areas of Expertise:
• -Service Steps
• -Staff management tools
• -S.O.P
• -P&L Management
• -Inventory
• -P.O.S
• -Bar Menu
• -Mystery Shopper Service
• -Handling and Managing Suppliers

```html
<!DOCTYPE html>
<html lang="en">
<head>
<meta charset="utf-8">
<title>Q&amp;T Consulting Business Cards</title>
<link href="https://fonts.googleapis.com/css2?family=Roboto+Condensed:wght@400;700&display=swap" rel="stylesheet">
<style>
  :root {
    --backdrop: #e9e6e1;
    --card-black: #151515;
    --card-white: #f7f7f7;
    --stripe-grey: #8c8c8c;
    --stripe-light: #c9c9c9;
    --ink-white: #ffffff;
    --ink-black: #151515;
    --badge-fill: #d9d9d9;
  }
  * { margin: 0; padding: 0; box-sizing: border-box; }
  html, body {
    width: 1200px; height: 911px; overflow: hidden;
    background: var(--backdrop);
    font-family: "Roboto Condensed", sans-serif;
  }
  .sheet { position: relative; width: 1200px; height: 911px; }
  .card {
    position: absolute; left: 250px; width: 700px; height: 400px;
    border-radius: 22px; overflow: hidden;
    box-shadow: 0 12px 30px rgba(0,0,0,.25);
  }
  .card--front { top: 40px; background: var(--card-white); }
  .card--back { top: 470px; background: var(--card-black); color: var(--ink-white); }
  .front-swoosh { position: absolute; inset: 0; }
  .brand-name { font-weight: 700; letter-spacing: 1px; white-space: nowrap; }
  .card--front .brand {
    position: absolute; left: 50px; top: 160px;
    color: var(--ink-black);
  }
  .card--front .brand-name { font-size: 40px; }
  .contact {
    position: absolute; right: 36px; top: 70px; text-align: right;
    color: var(--ink-white);
  }
  .contact-name { font-size: 28px; font-weight: 700; text-transform: uppercase; white-space: nowrap; }
  .contact-company { font-size: 21px; text-transform: uppercase; letter-spacing: 1px; margin-top: 4px; }
  .contact-line {
    display: flex; justify-content: flex-end; align-items: center; gap: 10px;
    font-size: 19px; margin-top: 24px; white-space: nowrap;
  }
  .contact-line + .contact-line { margin-top: 10px; }
  .contact-line svg { width: 18px; height: 18px; }
  .card--back .brand {
    position: absolute; left: 0; right: 0; top: 70px;
    display: flex; justify-content: center; align-items: center;
  }
  .card--back .brand-name { font-size: 60px; }
  .expertise { position: absolute; left: 0; right: 0; top: 190px; text-align: center; }
  .expertise-title { font-size: 26px; font-weight: 700; margin-bottom: 12px; }
  .expertise-list { font-size: 20px; line-height: 1.4; }
  .badges {
    position: absolute; right: 24px; top: 36px;
    display: flex; flex-direction: column; gap: 10px;
  }
  .badge { width: 44px; height: 44px; border-radius: 50%; background: var(--badge-fill); }
</style>
</head>
<body>
<main class="sheet">
  <section class="card card--front">
    <svg class="front-swoosh" viewBox="0 0 700 400" preserveAspectRatio="none">
      <path d="M384 0 C 304 104, 286 288, 234 400 L 700 400 L 700 0 Z" fill="var(--stripe-light)"/>
      <path d="M396 0 C 316 104, 298 288, 246 400 L 700 400 L 700 0 Z" fill="var(--stripe-grey)"/>
      <path d="M410 0 C 330 104, 312 288, 260 400 L 700 400 L 700 0 Z" fill="var(--card-white)"/>
      <path d="M420 0 C 340 104, 322 288, 270 400 L 700 400 L 700 0 Z" fill="var(--card-black)"/>
    </svg>
    <div class="brand">
      <span class="brand-name">Q&amp;T Meridian</span>
    </div>
    <div class="contact">
      <p class="contact-name">Mathieu Girardot</p>
      <p class="contact-company">Q&amp;T Consulting</p>
      <p class="contact-line">15027390614
        <svg viewBox="0 0 24 24" aria-hidden="true"><path fill="#fff" d="M6.6 10.8a15 15 0 0 0 6.6 6.6l2.2-2.2a1 1 0 0 1 1-.25 11.4 11.4 0 0 0 3.6.57 1 1 0 0 1 1 1V20a1 1 0 0 1-1 1A17 17 0 0 1 3 4a1 1 0 0 1 1-1h3.5a1 1 0 0 1 1 1c0 1.250.2 2.450.57 3.6a1 1 0 0 1-.25 1z"/></svg>
      </p>
      <p class="contact-line">mathqt@sampleinbox.com
        <svg viewBox="0 0 24 24" aria-hidden="true"><rect x="2" y="5" width="20" height="14" rx="2" fill="#fff"/><path d="M3 6l9 7 9-7" fill="none" stroke="#151515" stroke-width="2"/></svg>
      </p>
    </div>
  </section>

  <section class="card card--back">
    <div class="brand">
      <span class="brand-name">Q&amp;T Meridian</span>
    </div>
    <div class="badges">
      <span class="badge"></span>
      <span class="badge"></span>
      <span class="badge"></span>
    </div>
    <div class="expertise">
      <h2 class="expertise-title">Areas of Expertise</h2>
      <p class="expertise-list">Service Steps | Staff management tools | S.O.P | P&amp;L Management</p>
      <p class="expertise-list">Inventory | P.O.S | Bar Menu | Mystery Shopper Service</p>
      <p class="expertise-list">Handling and Managing Suppliers</p>
    </div>
  </section>
</main>
</body>
</html>
```